Webdesign für neue Weinmarke
Zielgruppe
Kelchwandler ist eine neue Weinmarke. Es wird vorerst drei grundlegende Sorten geben: einen Rotwein, einen Weißwein und einen Rosé. Für diese neue Weinmarke wollen wir eine Webseite gestalten, welche die Weine ansprechend darstellt und zusätzlich den Kunden die Möglichkeit gibt, mehr Informationen über den Wein einzuholen. Die Marke Kelchwandler ist auch im Etikett an den Graf von Tressenbach angelehnt. Das Etikett zeigt den Baron, wie er auf einem Weinfass reitet – daher der Name „Kelchwandler“. Die Story, die wir mit dem Wein spielen, ist, dass die besonderen Fähigkeiten des Barons auch auf den Genuss des Kelchwandler zurückzuführen sind.
Die Zielgruppe für den Kelchwandler ist breit gefächert und schließt per se erst mal keine Personengruppe aus. Der Wein soll eher im niedrigeren Preissegment verkauft werden.
Aufgabenstellung
Es soll eine neue Webseite designt werden, die sich im Aufbau an der die Webseite http://www.velgor-example.de/#!/de/unsere-weine/sortiment orientieren kann. Zudem können für die Entwicklung kleine Animationen berücksichtigt werden, die die Seite auflockern. Das Design soll eine responsive Webseite unterstützen. Das Design soll zur Weinmarke Kelchwandler passen von der wir bisher nur das Etikett haben.

```html
<!DOCTYPE html>
<html lang="de">
<head>
<meta charset="utf-8">
<title>Kelchwandler – Webdesign</title>
<link rel="stylesheet" href="https://fonts.googleapis.com/css2?family=Open+Sans+Condensed:wght@700&family=Open+Sans:wght@400;600&display=swap">
<style>
  :root {
    --page-bg: #ffffff;
    --paper: #efece3;
    --paper-shade: #ddd6c6;
    --ink: #2b2b2b;
    --nav-ink: #555049;
    --white: #ffffff;
    --red-band: #7e3326;
    --red-bar: #5f261d;
    --rose-band: #dc5c5e;
    --rose-bar: #a8454a;
    --green-band: #a6c04a;
    --green-bar: #7f9139;
    --bottle-riesling: #b8b24c;
    --bottle-dark: #2a2530;
    --bottle-rose: #e0364a;
  }
  * { box-sizing: border-box; margin: 0; padding: 0; }
  html, body { width: 720px; height: 1200px; overflow: hidden; background: var(--page-bg); }
  body { font-family: "Open Sans", Arial, sans-serif; }

  .showcase {
    width: 720px; height: 1200px;
    padding: 10px 56px;
    display: flex; flex-direction: column; gap: 20px;
  }

  .screen {
    position: relative;
    width: 608px; height: 380px;
    overflow: hidden;
    background: var(--paper);
  }
  .screen--red   { --band: var(--red-band);   --bar: var(--red-bar); }
  .screen--rose  { --band: var(--rose-band);  --bar: var(--rose-bar); }
  .screen--green { --band: var(--green-band); --bar: var(--green-bar); }

  .landscape {
    position: absolute; left: 0; top: 0; width: 608px; height: 198px;
    background: linear-gradient(180deg, var(--paper) 20%, var(--paper-shade) 100%);
  }
  .baron-art {
    position: absolute; left: 128px; top: 44px; width: 182px; height: 154px;
    background: radial-gradient(ellipse at 45% 55%, #4a4743 0%, #8d8880 60%, rgba(141,136,128,0) 100%);
    border-radius: 40% 40% 0 0;
  }

  .site-header { position: absolute; left: 69px; right: 70px; top: 19px; display: flex; justify-content: space-between; align-items: center; }
  .brand {
    font-family: "Open Sans Condensed", "Arial Narrow", sans-serif;
    font-weight: 700; font-size: 14px; letter-spacing: 0.5px; color: var(--ink);
  }
  .main-nav { display: flex; gap: 9px; margin-top: 4px; }
  .main-nav a {
    font-size: 6px; letter-spacing: 0.3px; color: var(--nav-ink); text-decoration: none; text-transform: uppercase;
  }
  .main-nav a.is-muted { color: #8a8379; }

  .hero-band {
    position: absolute; left: 0; top: 198px; width: 608px; height: 152px;
    background: var(--band);
  }
  .hero-copy { position: absolute; left: 69px; top: 230px; width: 230px; color: var(--white); }
  .hero-title {
    font-family: "Open Sans Condensed", "Arial Narrow", sans-serif;
    font-weight: 700; font-size: 15px; line-height: 14.5px; text-transform: uppercase;
  }
  .hero-text { margin-top: 9px; font-size: 6.6px; line-height: 10px; }
  .hero-link {
    display: inline-flex; align-items: center; gap: 6px; margin-top: 15px;
    font-family: "Open Sans Condensed", "Arial Narrow", sans-serif;
    font-weight: 700; font-size: 7px; color: var(--white); text-decoration: none; text-transform: uppercase;
  }

  .bottle {
    position: absolute; width: 48px;
    border-radius: 9px 9px 6px 6px;
    box-shadow: 0 6px 10px rgba(0,0,0,0.25);
  }
  .bottle--left   { left: 329px; top: 95px;  height: 228px; }
  .bottle--center { left: 400px; top: 88px;  height: 242px; width: 52px; }
  .bottle--right  { left: 471px; top: 95px;  height: 228px; }
  .bottle--riesling { background: linear-gradient(90deg, #8f8a34, var(--bottle-riesling) 45%, #d8d38a 60%, #8f8a34); }
  .bottle--dark     { background: linear-gradient(90deg, #17141b, var(--bottle-dark) 45%, #4d4655 60%, #17141b); }
  .bottle--rose     { background: linear-gradient(90deg, #a8202f, var(--bottle-rose) 45%, #f07685 60%, #a8202f); }

  .wine-tabs {
    position: absolute; left: 0; top: 350px; width: 608px; height: 30px;
    background: var(--bar);
    display: grid; grid-template-columns: 1fr 1fr 1fr; align-items: center; text-align: center;
  }
  .wine-tabs span {
    font-family: "Open Sans Condensed", "Arial Narrow", sans-serif;
    font-weight: 700; font-size: 7.5px; text-transform: uppercase; color: rgba(255,255,255,0.55);
  }
  .wine-tabs .is-active { color: var(--white); }
  .tab-pointer { position: absolute; left: 298px; top: 344px; }
</style>
</head>
<body>
<main class="showcase">

  <section class="screen screen--red">
    <div class="landscape" role="img" aria-label="Gezeichnete Weinberglandschaft"></div>
    <div class="baron-art" role="img" aria-label="Kupferstich-Illustration des Grafen mit Weinglas"></div>
    <header class="site-header">
      <span class="brand">KELCHWANDLER</span>
      <nav class="main-nav"><a href="#">Home</a><a href="#">Rotwein</a><a href="#">Rosé</a><a href="#">Weißwein</a><a class="is-muted" href="#">Regionen</a><a class="is-muted" href="#">Der Baron</a></nav>
    </header>
    <div class="hero-band"></div>
    <div class="hero-copy">
      <h2 class="hero-title">Der Wein, der schon dem Baron selbst Anmut &amp; Heldengeist verlieh</h2>
      <p class="hero-text">Genießen Sie Kelchwandler als gehaltvollen und fruchtbetonten Rotwein, als lieblichen und fruchtigen Rosé oder als feinherben Riesling. Die drei Weine überzeugen durch höchste Qualität, harmonische Säuren und ein außergewöhnliches Design.</p>
      <a class="hero-link" href="#">Zu den Produkten <svg width="9" height="7" viewBox="0 0 9 7"><path d="M0 3.5h8M5 0.5l3 3-3 3" fill="none" stroke="#fff" stroke-width="1"/></svg></a>
    </div>
    <div class="bottle bottle--left bottle--riesling" role="img" aria-label="Flasche Riesling feinherb"></div>
    <div class="bottle bottle--center bottle--dark" role="img" aria-label="Flasche Dornfelder halbtrocken"></div>
    <div class="bottle bottle--right bottle--rose" role="img" aria-label="Flasche Dornfelder Rosé"></div>
    <svg class="tab-pointer" width="12" height="6" viewBox="0 0 12 6"><path d="M0 6L6 0l6 6z" fill="var(--bar)"/></svg>
    <nav class="wine-tabs"><span>Dornfelder Rosé</span><span class="is-active">Dornfelder halbtrocken</span><span>Riesling feinherb</span></nav>
  </section>

  <section class="screen screen--rose">
    <div class="landscape" role="img" aria-label="Gezeichnete Weinberglandschaft"></div>
    <div class="baron-art" role="img" aria-label="Kupferstich-Illustration des Grafen mit Weinglas"></div>
    <header class="site-header">
      <span class="brand">KELCHWANDLER</span>
      <nav class="main-nav"><a href="#">Home</a><a href="#">Rotwein</a><a href="#">Rosé</a><a href="#">Weißwein</a><a class="is-muted" href="#">Regionen</a><a class="is-muted" href="#">Der Baron</a></nav>
    </header>
    <div class="hero-band"></div>
    <div class="hero-copy">
      <h2 class="hero-title">Der Wein, der schon dem Baron selbst Anmut &amp; Heldengeist verlieh</h2>
      <p class="hero-text">Genießen Sie Kelchwandler als gehaltvollen und fruchtbetonten Rotwein, als lieblichen und fruchtigen Rosé oder als feinherben Riesling. Die drei Weine überzeugen durch höchste Qualität, harmonische Säuren und ein außergewöhnliches Design.</p>
      <a class="hero-link" href="#">Zu den Produkten <svg width="9" height="7" viewBox="0 0 9 7"><path d="M0 3.5h8M5 0.5l3 3-3 3" fill="none" stroke="#fff" stroke-width="1"/></svg></a>
    </div>
    <div class="bottle bottle--left bottle--dark" role="img" aria-label="Flasche Dornfelder halbtrocken"></div>
    <div class="bottle bottle--center bottle--rose" role="img" aria-label="Flasche Dornfelder Rosé"></div>
    <div class="bottle bottle--right bottle--riesling" role="img" aria-label="Flasche Riesling feinherb"></div>
    <svg class="tab-pointer" width="12" height="6" viewBox="0 0 12 6"><path d="M0 6L6 0l6 6z" fill="var(--bar)"/></svg>
    <nav class="wine-tabs"><span>Dornfelder halbtrocken</span><span class="is-active">Dornfelder Rosé</span><span>Riesling feinherb</span></nav>
  </section>

  <section class="screen screen--green">
    <div class="landscape" role="img" aria-label="Gezeichnete Weinberglandschaft"></div>
    <div class="baron-art" role="img" aria-label="Kupferstich-Illustration des Grafen mit Weinglas"></div>
    <header class="site-header">
      <span class="brand">KELCHWANDLER</span>
      <nav class="main-nav"><a href="#">Home</a><a href="#">Rotwein</a><a href="#">Rosé</a><a href="#">Weißwein</a><a class="is-muted" href="#">Regionen</a><a class="is-muted" href="#">Der Baron</a></nav>
    </header>
    <div class="hero-band"></div>
    <div class="hero-copy">
      <h2 class="hero-title">Der Wein, der schon dem Baron selbst Anmut &amp; Heldengeist verlieh</h2>
      <p class="hero-text">Genießen Sie Kelchwandler als gehaltvollen und fruchtbetonten Rotwein, als lieblichen und fruchtigen Rosé oder als feinherben Riesling. Die drei Weine überzeugen durch höchste Qualität, harmonische Säuren und ein außergewöhnliches Design.</p>
      <a class="hero-link" href="#">Zu den Produkten <svg width="9" height="7" viewBox="0 0 9 7"><path d="M0 3.5h8M5 0.5l3 3-3 3" fill="none" stroke="#fff" stroke-width="1"/></svg></a>
    </div>
    <div class="bottle bottle--left bottle--dark" role="img" aria-label="Flasche Dornfelder halbtrocken"></div>
    <div class="bottle bottle--center bottle--riesling" role="img" aria-label="Flasche Riesling feinherb"></div>
    <div class="bottle bottle--right bottle--rose" role="img" aria-label="Flasche Dornfelder Rosé"></div>
    <svg class="tab-pointer" width="12" height="6" viewBox="0 0 12 6"><path d="M0 6L6 0l6 6z" fill="var(--bar)"/></svg>
    <nav class="wine-tabs"><span>Dornfelder halbtrocken</span><span class="is-active">Riesling feinherb</span><span>Dornfelder Rosé</span></nav>
  </section>

</main>
</body>
</html>
```